Dalvick's Business Card

I need some designs for a new business card including the new logo attached. An old example of our business card is also attached to show all the data that should be included on the new design.
**I added some more examples someone had mocked up**

Contact Information for Business Card

Should include all info on other examples uploaded.

```html
<!DOCTYPE html>
<html lang="en">
<head>
<meta charset="utf-8">
<title>Dalvick's Business Card</title>
<link rel="stylesheet" href="https://fonts.googleapis.com/css2?family=Montserrat:wght@400;500;600;700&display=swap">
<style>
  :root {
    --brand-blue: #1068b7;
    --card-blue: #0b6cbc;
    --brand-red: #e0262b;
    --ink: #2a2a2a;
    --white: #ffffff;
    --backdrop: #e9e6e1;
  }
  * { box-sizing: border-box; margin: 0; padding: 0; }
  html, body { width: 900px; height: 1200px; overflow: hidden; }
  body {
    background: var(--backdrop);
    font-family: "Montserrat", sans-serif;
    position: relative;
  }
  .card {
    position: absolute;
    left: 80px;
    width: 742px;
    height: 440px;
    border-radius: 30px;
    overflow: hidden;
    box-shadow: 0 6px 14px rgba(0,0,0,0.35);
  }
  .card-front { top: 132px; background: var(--white); }
  .card-back { top: 640px; background: var(--card-blue); }

  .brand {
    position: absolute;
    display: flex;
    align-items: center;
    font-weight: 600;
    white-space: nowrap;
  }
  .brand-dot { border-radius: 50%; flex: none; }
  .card-front .brand {
    left: 34px; top: 182px;
    font-size: 46px; color: var(--brand-blue);
    gap: 14px;
  }
  .card-front .brand-dot { width: 22px; height: 22px; background: var(--brand-red); }
  .card-back .brand {
    left: 0; right: 0; top: 174px;
    justify-content: center;
    font-size: 68px; color: var(--white);
    gap: 20px;
  }
  .card-back .brand-dot { width: 30px; height: 30px; background: var(--brand-red); }

  .divider {
    position: absolute;
    left: 412px; top: 146px;
    width: 2px; height: 152px;
    background: var(--brand-blue);
  }
  .contact { position: absolute; left: 450px; top: 140px; color: var(--ink); }
  .contact-name {
    font-size: 26px; font-weight: 700; color: var(--brand-blue);
    margin-bottom: 16px;
  }
  .service-area { font-size: 15.5px; line-height: 20px; margin-bottom: 22px; }
  .contact-line {
    display: flex; align-items: center; gap: 10px;
    font-size: 16px; line-height: 23px;
  }
  .contact-line svg { width: 16px; height: 14px; flex: none; }

  .ribbon {
    position: absolute; left: 0; bottom: 0;
    width: 742px; height: 41px;
  }
  .ribbon-label {
    position: absolute; bottom: 0; height: 41px;
    display: flex; align-items: center; justify-content: center;
    color: var(--white); font-size: 15.5px; font-weight: 500;
    letter-spacing: 0.2px;
  }
  .ribbon-left { left: 0; width: 408px; }
  .ribbon-right { left: 400px; width: 310px; }

  .call-line {
    position: absolute; left: 0; right: 0; top: 382px;
    text-align: center; color: var(--white);
    font-size: 16px; font-weight: 500; letter-spacing: 0.1px;
  }
</style>
</head>
<body>
  <section class="card card-front">
    <div class="brand"><span class="brand-dot"></span>DALVICK'S</div>
    <div class="divider"></div>
    <div class="contact">
      <p class="contact-name">Mark Dalvick</p>
      <p class="service-area">Serves Fairview<br>IA &amp; Surrounding Areas</p>
      <p class="contact-line">
        <svg viewBox="0 0 16 14" aria-hidden="true"><path fill="#e0262b" d="M2 3c0-2 12-2 12 0v2h-3V3.6H5V5H2zM3 6h10l1 7H2zm5 1.6a2 2 0 1 0 0 4 2 2 0 0 0 0-4z"/></svg>
        555.014.2290
      </p>
      <p class="contact-line">
        <svg viewBox="0 0 16 14" aria-hidden="true"><path fill="#1068b7" d="M1 2h14v10H1zm1.5 1.5L8 8l5.5-4.5z" fill-rule="evenodd"/></svg>
        hvacdalvick@mailbox.com
      </p>
    </div>
    <svg class="ribbon" viewBox="0 0 742 41" aria-hidden="true">
      <polygon points="0,0 398,0 378,41 0,41" fill="#1068b7"/>
      <polygon points="406,0 742,0 742,41 386,41" fill="#e0262b"/>
    </svg>
    <span class="ribbon-label ribbon-left">FAMILY OWNED &amp; OPERATED</span>
    <span class="ribbon-label ribbon-right">LICENSED &amp; INSURED</span>
  </section>

  <section class="card card-back">
    <div class="brand"><span class="brand-dot"></span>DALVICK'S</div>
    <p class="call-line">CALL TODAY FOR ALL YOUR HVAC, REFRIGERATION &amp; PLUMBING NEEDS</p>
  </section>
</body>
</html>
```